Executive recruiting firm in need of business card design

Executive recruiting firm looking for a sleek, classy and modern business card design; card itself will be square shape, rounded edges and soft touch paper, our colors are dark blues in the navy color scale, silvers and grays. Reference our website for a better idea of our company's feel and goals at Tarvex-Up.com - our company message is "Employee Engagement Begins at Recruitment" this should be on the card

```html
<!DOCTYPE html>
<html lang="en">
<head>
<meta charset="utf-8">
<title>Tarvex Up — Business Card</title>
<link rel="stylesheet" href="https://fonts.googleapis.com/css2?family=Montserrat:wght@300;400&family=Roboto:ital,wght@0,300;1,400;1,700&display=swap">
<style>
  :root {
    --navy: #1d1b57;
    --navy-soft: #23216a;
    --white: #ffffff;
    --paper: #fbfbfb;
    --silver: #9a9aa3;
    --ghost: #f1f1f2;
    --backdrop: #d9d9db;
  }
  * { box-sizing: border-box; margin: 0; padding: 0; }
  html, body { width: 1200px; height: 900px; overflow: hidden; }
  body {
    background: var(--backdrop);
    font-family: "Montserrat", sans-serif;
    position: relative;
  }
  .card {
    position: absolute;
    left: 290px;
    width: 620px;
    height: 360px;
    box-shadow: 0 8px 24px rgba(0,0,0,0.18);
  }
  /* Back side */
  .card-back { top: 50px; background: var(--navy); color: var(--white); overflow: hidden; }
  .card-back .pattern-field {
    position: absolute; inset: 0;
    background: var(--navy-soft);
  }
  .brand {
    position: absolute;
    display: flex; align-items: center; gap: 10px;
    font-family: "Montserrat", sans-serif; font-weight: 300;
  }
  .brand-name { letter-spacing: 6px; line-height: 1; white-space: nowrap; }
  .brand-sub { display: block; font-size: 7px; letter-spacing: 3px; margin-top: 6px; }
  .brand-dot { border-radius: 50%; flex: none; }
  .card-back .brand { left: 150px; top: 120px; color: var(--white); }
  .card-back .brand-name { font-size: 40px; }
  .card-back .brand-dot { width: 86px; height: 86px; background: var(--white); }
  .tagline {
    position: absolute; left: 0; right: 0; bottom: 40px;
    text-align: center; font-size: 14px; font-weight: 300; letter-spacing: 1px;
  }
  /* Front side */
  .card-front { top: 470px; background: var(--paper); color: var(--navy); overflow: hidden; }
  .name-tab { position: absolute; left: 0; top: 30px; width: 8px; height: 32px; background: var(--navy); }
  .person { position: absolute; left: 40px; top: 30px; font-family: "Roboto", sans-serif; }
  .person-name { font-size: 21px; font-weight: 700; font-style: italic; }
  .person-role { font-size: 14px; font-style: italic; color: #333; font-weight: 400; }
  .card-front .brand { right: 42px; top: 80px; color: var(--navy); }
  .card-front .brand-name { font-size: 30px; }
  .card-front .brand-dot { width: 66px; height: 66px; background: var(--navy); }
  .ghost-disc { position: absolute; right: 60px; top: 170px; width: 200px; height: 200px; border-radius: 50%; background: var(--ghost); }
  .address {
    position: absolute; left: 70px; top: 178px;
    font-size: 15px; font-weight: 300; color: var(--silver); line-height: 1.3;
  }
  .contact-list { position: absolute; left: 48px; top: 240px; list-style: none; }
  .contact-list li {
    display: flex; align-items: center; gap: 14px;
    font-family: "Roboto", sans-serif; font-weight: 300; font-size: 17px; color: #555; height: 24px;
  }
  .contact-list svg { width: 14px; height: 14px; fill: var(--navy); flex: none; }
  .base-band { position: absolute; left: 0; right: 0; bottom: 0; height: 36px; background: var(--navy); }
  .band-dot { position: absolute; left: 22px; top: 4px; width: 28px; height: 28px; border-radius: 50%; border: 2px solid var(--white); }
</style>
</head>
<body>
  <section class="card card-back">
    <div class="pattern-field" role="img" aria-label="Repeating pattern of small faint brand circles across the navy back"></div>
    <div class="brand">
      <div>
        <span class="brand-name">TARVEX UP</span>
        <span class="brand-sub">talent acquisition</span>
      </div>
      <span class="brand-dot"></span>
    </div>
    <p class="tagline">Employee Engagement Begins at Recruitment</p>
  </section>

  <section class="card card-front">
    <span class="name-tab"></span>
    <div class="person">
      <p class="person-name">Maren Ellery</p>
      <p class="person-role">Founder</p>
    </div>
    <div class="brand">
      <div>
        <span class="brand-name">TARVEX UP</span>
        <span class="brand-sub">talent acquisition</span>
      </div>
      <span class="brand-dot"></span>
    </div>
    <span class="ghost-disc"></span>
    <p class="address">418 Harlow Street Suite #<br>1207 Brookfield NY 10512</p>
    <ul class="contact-list">
      <li>
        <svg viewBox="0 0 16 16"><path d="M3 1l3 3-1.5 2a9 9 0 0 0 5.5 5.5L12 10l3 3-2 2C7 15 1 9 1 3z"/></svg>
        +1.555.014.2290
      </li>
      <li>
        <svg viewBox="0 0 16 16"><path d="M4 0h8a1 1 0 0 1 1 1v14a1 1 0 0 1-1 1H4a1 1 0 0 1-1-1V1a1 1 0 0 1 1-1zm1 2v10h6V2z"/></svg>
        555-014-7736
      </li>
      <li>
        <svg viewBox="0 0 16 16"><path d="M0 3h16v10H0zm1 1.2v.3l7 5 7-5v-.3z"/></svg>
        mellery@tarvex-up.com
      </li>
    </ul>
    <div class="base-band"><span class="band-dot"></span></div>
  </section>
</body>
</html>
```